Harborview Estates Business Card for Apartment Buildings

Create business cards for resident managers who run apartment buildings. The audience is the public who are searching for apartment rentals, and current residents who live at the apartment building. Key design element will be incorporating the company logo, however, the logo cannot dominate. The building name and manager name are more important than the logo. Current business card design leaves little room for copy, so we may need to reduce the size on the current card to allow for more space for copy.

Target Market(s)

Adults 18-65 years of age, who are looking for an apartment rental, plus current residents who live at our apartment buildings.

Industry/Entity Type

Property Management

Contact Information for Business Card

A major design element will be use of the company logo. Important property and manager contact information must be part of the design. The size of the logo will need to be reduced to make room for building and manager contact copy.

Font styles to use
Sans Serif

Colors
3176b5
000000
959595
ffffff

Requirements
Must have
• 1) Incorporate the company logo.
• 2) Use the company colors (dark blue, black/grey, over white).
• 3) FEATURE THE BUILDING NAME
• 4) FEATURE THE MANAGER NAME
• 5) The company name is less important than BUILDING and MANAGER
• 6) Manager contact information
• **SEE ATTACHED CREATIVE BRIEF**
Nice to have
• 1) Back of card logo watermark
• 2) Ability to write notes on back of carfd
Should not have
• Avoid letting the company logo dominate the card, the building name and manager are more important than the company logo.

```html
<!DOCTYPE html>
<html lang="en">
<head>
<meta charset="utf-8">
<title>Harborview Estates Business Card</title>
<link rel="stylesheet" href="https://fonts.googleapis.com/css2?family=Lato:wght@400;700;900&display=swap">
<style>
:root{
  --brand-blue:#1f6fb2;
  --ink:#2b2b2b;
  --grey:#555a5f;
  --grey-band:#4a4d52;
  --white:#ffffff;
  --backdrop:#1c1c1e;
}
*{box-sizing:border-box;margin:0;padding:0}
html,body{width:1200px;height:852px;overflow:hidden}
body{
  background:var(--backdrop);
  font-family:"Lato",Arial,sans-serif;
  display:flex;align-items:center;justify-content:center;gap:40px;
}
.card{
  position:relative;width:540px;height:309px;border-radius:16px;overflow:hidden;
  box-shadow:0 10px 30px rgba(0,0,0,.5);
}
/* front */
.card-front{background:var(--brand-blue);color:var(--white)}
.card-front .brand{
  position:absolute;left:0;right:0;top:96px;
  display:flex;align-items:center;justify-content:center;gap:16px;
}
.card-front .brand-mark{width:44px;height:44px;background:var(--white);flex:none}
.card-front .brand-name{
  font-weight:900;font-size:36px;letter-spacing:1px;text-transform:uppercase;line-height:1.05;
}
.card-front .site{
  position:absolute;left:0;right:0;top:232px;text-align:center;font-size:14px;letter-spacing:.5px;
}
/* back */
.card-back{background:var(--white);color:var(--ink)}
.card-back .swoosh{position:absolute;left:0;bottom:0}
.card-back .brand{
  position:absolute;left:34px;top:58px;
  font-weight:900;font-size:22px;color:var(--brand-blue);text-transform:uppercase;line-height:1.1;
}
.manager{position:absolute;left:34px;top:140px}
.manager .name{font-weight:700;font-size:22px;color:var(--brand-blue)}
.manager .title{font-size:13px;color:var(--grey);margin-top:1px}
.rule{position:absolute;height:1.5px;background:var(--brand-blue)}
.rule-left{left:34px;top:190px;width:210px}
.rule-right{left:300px;top:112px;width:210px}
.contact-list{position:absolute;list-style:none;font-size:13.5px;color:var(--ink)}
.contact-list li{display:flex;align-items:center;gap:10px;line-height:21px}
.contact-list svg{width:11px;height:11px;fill:var(--brand-blue);flex:none}
.phones{left:34px;top:200px}
.online{left:300px;top:62px;font-size:13px}
.property{position:absolute;left:300px;top:124px}
.property .building{font-weight:700;font-size:17px;color:var(--brand-blue)}
.property .address{font-size:13.5px;color:var(--ink);line-height:19px;margin-top:2px}
</style>
</head>
<body>
  <section class="card card-front" aria-label="Card front">
    <div class="brand">
      <span class="brand-mark"></span>
      <span class="brand-name">Harborview<br>Estates LLC</span>
    </div>
    <div class="site">www.harborviewest.com</div>
  </section>

  <section class="card card-back" aria-label="Card back">
    <svg class="swoosh" width="540" height="309" viewBox="0 0 540 309" aria-hidden="true">
      <path d="M0 276 C170 300 330 236 540 206 L540 309 L0 309 Z" fill="var(--grey-band)"/>
      <path d="M0 286 C180 302 340 246 540 218 L540 309 L0 309 Z" fill="var(--white)"/>
      <path d="M0 293 C190 304 350 254 540 228 L540 309 L0 309 Z" fill="var(--brand-blue)"/>
    </svg>

    <div class="brand">Harborview<br>Estates LLC</div>

    <div class="manager">
      <div class="name">Marisol Navarro</div>
      <div class="title">Resident Manager</div>
    </div>
    <div class="rule rule-left"></div>
    <ul class="contact-list phones">
      <li><svg viewBox="0 0 12 12"><path d="M2 1l2 0 1 3-1.3 1a6 6 0 0 0 3.3 3.3L8 7l3 1v2a1 1 0 0 1-1 1A9 9 0 0 1 1 2a1 1 0 0 1 1-1z"/></svg>555-240-1187</li>
      <li><svg viewBox="0 0 12 12"><rect x="1" y="4" width="10" height="6" rx="1"/><rect x="3" y="1" width="6" height="3"/></svg>555-318-6642</li>
      <li><svg viewBox="0 0 12 12"><path d="M3 0h6a1 1 0 0 1 1 1v10a1 1 0 0 1-1 1H3a1 1 0 0 1-1-1V1a1 1 0 0 1 1-1zm0 2v7h6V2z"/></svg>555-406-9315</li>
    </ul>

    <ul class="contact-list online">
      <li><svg viewBox="0 0 12 12"><path d="M1 2h10v8H1z"/><path d="M1 2l5 4 5-4" fill="none" stroke="var(--white)" stroke-width="1"/></svg>marisol@harborviewest.com</li>
      <li><svg viewBox="0 0 12 12"><circle cx="6" cy="6" r="5.5"/></svg>www.harborviewest.com</li>
    </ul>
    <div class="rule rule-right"></div>
    <div class="property">
      <div class="building">Cedar Court Apartments</div>
      <div class="address">1482 Linden Avenue<br>Port Carver, CA 92011</div>
    </div>
  </section>
</body>
</html>
```